CREATE A BUSINESS CARD FOR A BOAT CLEANING SERVICE

WE ARE STARTING A NEW BOAT CLEANING BUSINESS. WE DIVE UNDERWATER TO CLEAN BOAT HULLS, JETTIES, UNDERWATER STRUCTURES ETC. WE ARE LOOKING FOR AN UPPERMARKET MODERN LOGO AND BUSINESS CARD AS ALOT OF OUR TARGET MARKET WILL BE HIGH END. YOU HAVE TO DESIGN A BUSINESS CARD AND LOGO SEPERATELY .
THE BUSINESS CARD DIMESNION MUST BE STANDARD SIZE.
The standard dimensions of a printed business card are 3.5 x 2 inches

Target Market(s)

UNDERWATER SERVICED

Industry/Entity Type

Business

Contact Information for Business Card

HOLLAND UNDERWATER SERVICES

Font styles to use
Serif

Colors

Designer to choose colors to be used in the design.

Requirements
Must have
• HOLLAND
Nice to have
• dark
Should not have
• more than 3 colors

```html
<!DOCTYPE html>
<html lang="en">
<head>
<meta charset="UTF-8">
<title>Holland Underwater Services — Business Card</title>
<link rel="stylesheet" href="https://fonts.googleapis.com/css2?family=Lato:wght@400;700;900&display=swap">
<style>
  :root {
    --blue: #1d5797;
    --grey: #a4a4a4;
    --grey-line: #9a9a9a;
    --ink: #1f1f1f;
    --paper: #ffffff;
    --stage: #ecebe8;
  }
  * { box-sizing: border-box; margin: 0; padding: 0; }
  html, body { width: 1200px; height: 900px; overflow: hidden; }
  body {
    background: var(--stage);
    font-family: "Lato", Arial, sans-serif;
    position: relative;
  }
  .card {
    position: absolute;
    top: 296px;
    width: 540px;
    height: 309px;
    overflow: hidden;
    box-shadow: 0 6px 18px rgba(0,0,0,0.12);
  }
  /* Back side */
  .card-back { left: 40px; background: var(--grey); color: var(--paper); }
  .back-name {
    position: absolute; left: 0; right: 0; top: 92px;
    text-align: center;
    font-weight: 900; font-size: 44px; letter-spacing: 3px;
    color: var(--paper);
  }
  .tagline {
    position: absolute; left: 0; right: 0; top: 210px;
    text-align: center;
    font-size: 13px; letter-spacing: 1px; line-height: 1.45;
    text-transform: uppercase;
  }
  /* Front side */
  .card-front { left: 620px; background: var(--paper); color: var(--ink); }
  .brand {
    position: absolute; right: 32px; top: 40px;
    display: flex; align-items: center; gap: 12px;
  }
  .brand-mark { width: 22px; height: 22px; background: var(--blue); }
  .brand-text { color: var(--blue); font-weight: 700; line-height: 1; }
  .brand-name { font-size: 42px; letter-spacing: 1px; }
  .brand-sub { font-size: 10.5px; letter-spacing: 2.6px; margin-top: 4px; }
  .rule { position: absolute; height: 1px; background: var(--grey-line); }
  .rule-top { left: 230px; right: 30px; top: 116px; }
  .rule-name { left: 230px; right: 140px; top: 158px; }
  .holder { position: absolute; left: 36px; top: 140px; }
  .holder-name { color: var(--blue); font-weight: 700; font-size: 20px; letter-spacing: 0.5px; }
  .holder-role { font-size: 15px; margin-top: 2px; }
  .contacts { position: absolute; left: 36px; top: 206px; list-style: none; font-size: 15px; }
  .contacts li { display: flex; align-items: center; gap: 8px; height: 22px; }
  .contacts svg { width: 13px; height: 13px; fill: var(--blue); }
  .address {
    position: absolute; right: 30px; top: 174px;
    text-align: right; font-size: 14px; line-height: 1.35;
  }
  .band { position: absolute; bottom: 0; height: 14px; }
  .band-blue { left: 0; width: 64%; background: var(--blue); }
  .band-grey { left: 64%; right: 0; background: var(--grey); }
</style>
</head>
<body>

<section class="card card-back" aria-label="Card back">
  <div class="back-name">HOLLAND</div>
  <p class="tagline">We dive underwater to clean boat hulls<br>jetties, underwater structures etc</p>
</section>

<section class="card card-front" aria-label="Card front">
  <div class="brand">
    <span class="brand-mark"></span>
    <div class="brand-text">
      <div class="brand-name">HOLLAND</div>
      <div class="brand-sub">UNDERWATER SERVICES</div>
    </div>
  </div>
  <div class="rule rule-top"></div>

  <div class="holder">
    <div class="holder-name">DANIEL MARSH</div>
    <div class="holder-role">Managing Director</div>
  </div>
  <div class="rule rule-name"></div>

  <div class="address">18, Harbour Quay Road<br>Portside Bay,30218</div>

  <ul class="contacts">
    <li>
      <svg viewBox="0 0 16 16" aria-hidden="true"><path d="M3 1h3l1.5 4-2 1.3a9 9 0 0 0 4.2 4.2L11 8.5l4 1.5v3a2 2 0 0 1-2 2A12 12 0 0 1 1 3a2 2 0 0 1 2-2z"/></svg>
      321 654 9870
    </li>
    <li>
      <svg viewBox="0 0 16 16" aria-hidden="true"><path d="M1 3h14v10H1z M1.5 3.5 8 9l6.5-5.5" stroke="#fff" stroke-width="1.2"/></svg>
      hello@hollanddive.com
    </li>
    <li>
      <svg viewBox="0 0 16 16" aria-hidden="true"><circle cx="8" cy="8" r="7"/><path d="M1 8h14M8 1c-3 4-3 10 0 14M8 1c3 4 3 10 0 14" stroke="#fff" stroke-width="1" fill="none"/></svg>
      www.hollanddive.com
    </li>
  </ul>

  <div class="band band-blue"></div>
  <div class="band band-grey"></div>
</section>

</body>
</html>
```